New Business Card Design Project

Use the flyer uploaded and website www.brightoakbuilders.com for inspiration.
List Our Services on Backside of business cards
Marcus Delling
Harborline Builders Inc.
Licensed General Contractors
858-471-6093

Contact Information for Business Card

Use the flyer uploaded and website www.brightoakbuilders.com for inspiration. List Our Services on Backside of business cards Marcus Delling Harborline Builders Inc. Licensed General Contractors 858-471-6093

```html
<!DOCTYPE html>
<html lang="en">
<head>
<meta charset="UTF-8">
<title>Harborline Builders – Business Card</title>
<link rel="stylesheet" href="https://fonts.googleapis.com/css2?family=Cormorant+Garamond:wght@400;500&family=Arimo:wght@400&display=swap">
<style>
  :root {
    --page-bg: #d9d9d9;
    --card-bg: #303030;
    --card-ink: #f1f1f1;
    --card-muted: #cfcfcf;
    --rule: #bdbdbd;
  }
  * { box-sizing: border-box; margin: 0; padding: 0; }
  html, body {
    width: 1200px;
    height: 800px;
    overflow: hidden;
    background: var(--page-bg);
  }
  .stage {
    width: 1200px;
    height: 800px;
    display: flex;
    align-items: center;
    justify-content: center;
    gap: 60px;
  }
  .card {
    position: relative;
    width: 525px;
    height: 300px;
    background: var(--card-bg);
    border-radius: 18px;
    color: var(--card-ink);
    overflow: hidden;
  }

  /* Front */
  .front .brand-square {
    position: absolute;
    left: 44px;
    top: 50px;
    width: 18px;
    height: 18px;
    border: 1.5px solid var(--card-ink);
  }
  .front .name {
    position: absolute;
    left: 44px;
    top: 150px;
    font-family: "Cormorant Garamond", serif;
    font-weight: 400;
    font-size: 25px;
    letter-spacing: 0.08em;
    text-transform: uppercase;
  }
  .front .name-rule {
    position: absolute;
    left: 44px;
    top: 190px;
    width: 72px;
    height: 1px;
    background: var(--rule);
  }
  .front .contact {
    position: absolute;
    left: 44px;
    top: 208px;
    font-family: "Arimo", sans-serif;
    font-size: 14px;
    line-height: 28px;
    color: var(--card-ink);
  }
  .contact .sep { margin: 0 7px; color: var(--card-muted); }

  /* Back */
  .back .services {
    position: absolute;
    left: 34px;
    top: 34px;
    list-style: none;
    font-family: "Arimo", sans-serif;
    font-size: 15px;
    line-height: 23.5px;
  }
  .services li { display: flex; align-items: center; }
  .services li::before {
    content: "";
    width: 8px;
    height: 8px;
    background: var(--card-ink);
    margin-right: 12px;
    flex: none;
  }
  .back .brand {
    position: absolute;
    right: 30px;
    top: 110px;
    width: 230px;
    text-align: center;
  }
  .brand .brand-square {
    display: block;
    width: 18px;
    height: 18px;
    border: 1.5px solid var(--card-ink);
    margin: 0 auto 14px;
  }
  .brand .brand-name {
    font-family: "Cormorant Garamond", serif;
    font-weight: 400;
    font-size: 22px;
    letter-spacing: 0.06em;
    text-transform: uppercase;
    line-height: 1.15;
  }
  .brand .brand-web {
    margin-top: 18px;
    font-family: "Cormorant Garamond", serif;
    font-weight: 400;
    font-size: 12px;
    letter-spacing: 0.16em;
    text-transform: uppercase;
    color: var(--card-muted);
  }
</style>
</head>
<body>
  <main class="stage">
    <section class="card front" aria-label="Business card front">
      <span class="brand-square" aria-hidden="true"></span>
      <h1 class="name">Marcus Delling</h1>
      <div class="name-rule"></div>
      <div class="contact">
        <p>858-471-6093<span class="sep">|</span>info@brightoakbuilders.com<span class="sep">|</span>www.brightoakbuilders.com</p>
        <p>Harborline Builders Inc.<span class="sep">|</span>Licensed General Contractors</p>
      </div>
    </section>

    <section class="card back" aria-label="Business card back">
      <ul class="services">
        <li>Remodel: Kitchen &amp; Bath</li>
        <li>Painting : Interior &amp; Exterior</li>
        <li>Flooring : Carpet, Vinyl, Wood</li>
        <li>Window &amp; Door Replacement</li>
        <li>Plumbing : Repairs &amp; Upgrades</li>
        <li>Energy- Efficient Upgrades</li>
        <li>Deck &amp; Patio Construction</li>
        <li>Water &amp; Mold Damage</li>
        <li>Garage Renovation</li>
      </ul>
      <div class="brand">
        <span class="brand-square" aria-hidden="true"></span>
        <p class="brand-name">Harborline Builders</p>
        <p class="brand-web">www.brightoakbuilders.com</p>
      </div>
    </section>
  </main>
</body>
</html>
```